Resident Guide for Senior Living Community

I need to create an informational magazine for residents that live in an Assisted Living community. This magazine is designed to educate the resident about the different service options and features that the community provides. I don't want to use any of the pictures in the Word Document - please use the uploaded picture instead. The final design should be both informational and elegant. The text in the word document is the actual text that needs to be used in the Resident Guide. Thanks!

Target Market(s)

Senior citizens and adult children (55 - 65 years old)

Industry/Entity Type

Assisted Living

Requirements
Must have
• Must be elegant - think Velmont Hargrove. Needs to have a lot of pictures and the logo must be used. The logo is the Plaque that says The Birch Lodge.
Nice to have
• The Word doucment is the old Resident Guide - we are looking for a refresh using the same content.
Should not have
• please do not use any pictures from the Word Document other than the Logo.

```html
<!DOCTYPE html>
<html lang="en">
<head>
<meta charset="utf-8">
<title>The Birch Lodge — Resident Guide Spread</title>
<link href="https://fonts.googleapis.com/css2?family=Old+Standard+TT:ital,wght@0,400;0,700;1,400&display=swap" rel="stylesheet">
<style>
  :root{
    --backdrop:#e8e2dc;
    --paper:#ffffff;
    --ink:#2a2522;
    --ink-soft:#6f6660;
    --gutter-shade:rgba(0,0,0,.10);
    --porch-wood:#a58a68;
    --porch-green:#8fb04a;
    --porch-leaf:#6f9a3d;
    --room-cream:#ece6dc;
    --room-white:#f7f5f1;
    --portrait-navy:#2e3a5a;
    --portrait-tan:#c9a982;
  }
  *{box-sizing:border-box;margin:0;padding:0}
  html,body{width:1200px;height:800px;overflow:hidden;background:var(--backdrop)}
  body{font-family:"Old Standard TT",serif;color:var(--ink)}
  .spread{position:absolute;left:40px;top:40px;width:1120px;height:720px;display:flex;box-shadow:0 10px 30px rgba(0,0,0,.18)}
  .page{position:relative;width:560px;height:720px;background:var(--paper);overflow:hidden}
  .page--left::after{content:"";position:absolute;right:0;top:0;width:40px;height:100%;background:linear-gradient(to left,var(--gutter-shade),transparent)}
  .page--right::before{content:"";position:absolute;left:0;top:0;width:30px;height:100%;background:linear-gradient(to right,var(--gutter-shade),transparent);z-index:2}
  .column{position:absolute;font-size:9.4px;line-height:13px;text-align:justify;hyphens:auto}
  .column p{margin-bottom:8px;text-indent:14px}
  .column p.no-indent{text-indent:0}
  .greeting{position:relative;padding-left:34px;margin-bottom:10px;font-style:italic;font-size:10.5px;line-height:13px;min-height:40px}
  .greeting .initial{position:absolute;left:0;top:-8px;font-size:48px;font-style:italic;color:#bdb6b0;line-height:1}
  .photo{position:absolute}
  .photo--porch-wide{left:210px;top:40px;width:350px;height:300px;background:linear-gradient(160deg,#5c6a34 0%,var(--porch-green) 35%,var(--porch-wood) 70%,#8a6f52 100%)}
  .photo--bedroom{left:210px;top:350px;width:350px;height:250px;background:linear-gradient(170deg,var(--room-white) 0%,var(--room-cream) 60%,#d9cfc0 100%)}
  .photo--porch-tall{left:0;top:40px;width:215px;height:360px;background:linear-gradient(180deg,var(--porch-leaf) 0%,#a9c57a 45%,#e9e6df 75%,#d8643a 100%)}
  .photo--portrait{left:0;top:410px;width:215px;height:190px;background:linear-gradient(160deg,#9a8a78 0%,var(--portrait-tan) 45%,var(--portrait-navy) 100%)}
  .signoff{margin-top:6px;font-style:italic;font-size:9.4px}
  .signature{display:block;margin-top:4px}
</style>
</head>
<body>
<main class="spread">
  <section class="page page--left">
    <div class="column column--letter" style="left:30px;top:44px;width:168px">
      <div class="greeting"><span class="initial">D</span>ear Friends, Families and our Special Residents</div>
      <p class="no-indent">The Birch Lodge is the fulfillment of a dream to honor the life's work of my father, and a determination to provide a superior level of care, dignity and lifestyle unique in the rapidly expanding field of residential health care. Forty years ago, my mother and I tried to find the kind of care and service The Birch Lodge offers for my Alzheimer's stricken father, but couldn't. It's a good feeling knowing we have made a real positive difference in the lives of hundreds of our residents and their families since we opened in 1988. We are here for one reason – to serve you and your family.</p>
      <p>We are different from most other Licensed Assisted Living (as differentiated from lower care level "personal care" facilities) homes in that, most importantly, we are a true Residential Healthcare Home specializing in quality health services, a health care model and secondarily, a social model. This distinction is crucial because, as your loved one ages, we have the trained, competent and essential staff members to handle their increasing health and personal health needs. Of course, we provide all the entertainment and stimulating activities, exercise programs, mental stimulation, etc. but from Day One of this family business we have focused on providing top-level health care services first and foremost, complemented by our solid social activity/hospitality schedule. Most other residential care facilities</p>
    </div>
    <div class="photo photo--porch-wide" role="img" aria-label="Photo of a sunlit covered porch with white wicker furniture, green cushions and wooden floorboards"></div>
    <div class="photo photo--bedroom" role="img" aria-label="Photo of a bright resident suite with a white bed, patterned pillow and dresser"></div>
  </section>

  <section class="page page--right">
    <div class="photo photo--porch-tall" role="img" aria-label="Photo of a screened porch with a green cushioned bench, orange throw and garden greenery"></div>
    <div class="photo photo--portrait" role="img" aria-label="Portrait photo of the founder and his wife standing together"></div>

    <div class="column" style="left:230px;top:44px;width:150px">
      <p class="no-indent">put their social program first and are primarily a social model giving less than full attention and importance (and financial support) to quality personal wellness and health care services. As you might expect, the health care model is much more expensive to implement and operate.</p>
      <p>Additionally, a true advantage our bundled services program for one inclusive monthly fee is that all services from personal care, medication management, meals, housekeeping, laundry and nursing visits are included, with no surprise add-on charges for the things your loved one needs each day.</p>
      <p>You'll be interested in knowing our extraordinary Care Staff to Resident ratio is among the very best, so residents are rarely asked to leave as their needs increase. We hope your family member will never have to move from The Birch Lodge.</p>
      <p>During the past nearly thirty (30) years our home has established a superior reputation, a tradition of excellence and an outstanding record of managing our residents' day-to-day healthcare needs, including Alzheimer's, Parkinson's, diabetes and recovery after a stroke or surgery.</p>
      <p>Further, setting us apart from most other residential health care homes who can no longer live independently.</p>
    </div>

    <div class="column" style="left:392px;top:44px;width:145px">
      <p class="no-indent">homes is our ability to care for couples, often with differing levels of independence and healthcare needs, enabling them to continue living together rather than be forced into separate facilities when one has greater requirements. This is something we've identified since 1988 as a real needed service and accommodation.</p>
      <p>There are many other features and benefits of The Birch Lodge, but these are most prominent: our small size of only 25 suites in Larkfield, our exceptional staff turnover, our 24-hour care, our 1:3 ratio and our central location.</p>
      <p>We set the standard for our industry, both in Brookvale and across the South. We sincerely realize that our responsibility is not only to your loved one, but to your entire family, and we strive every day to make living at The Birch Lodge the best possible alternative to living at home.</p>
      <p>Thank you for thinking of us. It would be a pleasure to meet you personally.</p>
      <p>Just call 555-014-2290 for an appointment. All best wishes to you and your family.</p>
      <p class="no-indent signoff">Founder and President</p>
      <svg class="signature" width="120" height="30" role="img" aria-label="Handwritten signature of the founder">
        <rect x="0" y="12" width="110" height="6" rx="3" fill="#d8d2cc"/>
      </svg>
    </div>
  </section>
</main>
</body>
</html>
```